Korrabel Ice Creamery tourist signage

We need to give passing tourists a snapshot of what great fun they can have visiting our brand new Ice creamery located in Timboon, 17km North of the Great Ocean Road and Famous 12 Apostles in Victoria Australia. So the sign needs to be more than directional, need to be enticing. needs to be designed in a manner that project quality. ( keep in mind cars travelling at 80km don't have a lot of time to read too much)
Size is 2.2metres wide by 1.4 meters high
This sign needs to be succinct. Needs to convey fun and a little indulgence but not in a 'tacky' or 'cheap' way.
Needs to offer indulgent imagery of course, our logo too and direction.

Target Market(s)

Tourists, domestic and internationals

Industry/Entity Type

Tourism

Font styles to use
Other font styles liked:
• sacred cow

Colors
add136
fdf3f8
b8a6cd
fabb94
fcca95
85acd3
fbf289

Requirements
Must have
• Convey fun, whimsy indulgence and value ( keeping in mind we need to entice these people a further 17km up the road!)
Nice to have
• White space and clear imagery with
Should not have
• Bold bling colours, be busy looking and cheap looking, needs to convey quality .

```html
<!DOCTYPE html>
<html lang="en">
<head>
<meta charset="utf-8">
<title>Korrabel Ice Creamery – Roadside Sign</title>
<link rel="stylesheet" href="https://fonts.googleapis.com/css2?family=Lato:wght@700;900&display=swap">
<style>
  :root {
    --lime: #e0ea2d;
    --berry: #a9262c;
    --berry-deep: #9b2126;
    --white: #ffffff;
    --ink: #1d1d1b;
    --leaf: #8cc63f;
    --cream: #fdf3f8;
    --strawberry: #f4c3cf;
    --peach: #fabb94;
    --dress: #a6d65c;
    --dress-deep: #8cc84a;
  }
  * { margin: 0; padding: 0; box-sizing: border-box; }
  html, body { width: 1200px; height: 764px; overflow: hidden; background: var(--lime); }
  .sign {
    position: relative;
    width: 1200px;
    height: 764px;
    background: var(--lime);
    font-family: "Lato", "Helvetica Neue", Arial, sans-serif;
    overflow: hidden;
  }
  .direction-band {
    position: absolute;
    left: 400px;
    top: 360px;
    width: 800px;
    height: 358px;
    background: linear-gradient(90deg, var(--berry-deep), var(--berry));
  }
  .hero-photo {
    position: absolute;
    left: 20px;
    top: 10px;
    width: 520px;
    height: 754px;
    border-radius: 260px 260px 0 0 / 240px 240px 0 0;
    background: linear-gradient(180deg,
      var(--cream) 0%,
      var(--strawberry) 38%,
      var(--peach) 56%,
      var(--dress) 70%,
      var(--dress-deep) 100%);
  }
  .brand {
    position: absolute;
    left: 680px;
    top: 68px;
    width: 340px;
    height: 120px;
    display: flex;
    align-items: center;
    justify-content: center;
    gap: 16px;
  }
  .brand-dot {
    width: 44px;
    height: 44px;
    border-radius: 50%;
    background: var(--leaf);
    flex: none;
  }
  .brand-name {
    color: var(--ink);
    font-weight: 900;
    font-size: 30px;
    line-height: 1.1;
    letter-spacing: 2px;
    text-transform: uppercase;
  }
  .tagline {
    position: absolute;
    left: 550px;
    top: 248px;
    width: 625px;
    text-align: center;
    color: var(--berry);
    font-weight: 900;
    font-size: 84px;
    line-height: 1;
    letter-spacing: -0.5px;
  }
  .distance {
    position: absolute;
    left: 545px;
    top: 392px;
    width: 610px;
    text-align: center;
    color: var(--white);
    font-weight: 900;
    font-size: 146px;
    line-height: 146px;
    letter-spacing: 1px;
  }
</style>
</head>
<body>
  <main class="sign">
    <div class="direction-band"></div>
    <div class="hero-photo" role="img" aria-label="Photo of a curly-haired toddler in a green dress happily licking a pink strawberry ice cream cone"></div>
    <div class="brand">
      <span class="brand-dot"></span>
      <span class="brand-name">Korrabel<br>Ice Creamery</span>
    </div>
    <p class="tagline">nom nom nom!</p>
    <p class="distance">17 KM<br>AHEAD</p>
  </main>
</body>
</html>
```